Local fast-growing company in the service sector

We are looking for a modern business card design, which should also appear on our letterheads

Target Market(s)

Private and industrial sectors

Contact Information for Business Card

Vorname Name
Kellberger Str. 18
73614 Schorndorf
Tel.: 07146-839214-0
Name@agentur-kvtl.de

Colors
9d9d9d
919191
aaaaaa

Requirements
Must have
• The logo (file) in silver

```html
<!DOCTYPE html>
<html lang="de">
<head>
<meta charset="utf-8">
<title>KVTL – Visitenkarte</title>
<link rel="stylesheet" href="https://fonts.googleapis.com/css2?family=Roboto:wght@400;500&family=Roboto+Condensed:wght@500;700&family=Michroma&display=swap">
<style>
  :root {
    --backdrop: #ece9e4;
    --card-dark: #1b1c1e;
    --card-light: #f3f3f3;
    --silver: #9d9d9d;
    --silver-mid: #919191;
    --silver-light: #aaaaaa;
    --text-dark: #4a4a4a;
    --white: #ffffff;
  }
  * { margin: 0; padding: 0; box-sizing: border-box; }
  html, body { width: 1200px; height: 960px; overflow: hidden; }
  body {
    background: var(--backdrop);
    position: relative;
    font-family: "Roboto", Arial, sans-serif;
  }
  .card {
    position: absolute;
    left: 320px;
    width: 600px;
    height: 344px;
    border-radius: 16px;
    overflow: hidden;
  }
  .card--front { top: 100px; background: var(--card-dark); }
  .card--back { top: 493px; background: var(--card-light); }

  .brand {
    position: absolute;
    display: flex;
    align-items: center;
    gap: 14px;
  }
  .brand__name {
    font-family: "Roboto Condensed", Arial, sans-serif;
    font-weight: 700;
    color: var(--silver-light);
    line-height: 1;
  }
  .brand__mark { background: var(--silver-light); flex-shrink: 0; }

  .card--front .brand { left: 36px; top: 214px; }
  .card--front .brand__name { font-size: 78px; }
  .card--front .brand__mark { width: 44px; height: 44px; }
  .front__web {
    position: absolute;
    left: 36px;
    top: 303px;
    font-size: 14px;
    letter-spacing: 3.2px;
    color: var(--white);
  }

  .card--back .brand { left: 28px; top: 50px; }
  .card--back .brand__name { font-size: 50px; color: var(--silver); }
  .card--back .brand__mark { width: 30px; height: 30px; background: var(--silver); }

  .contact {
    position: absolute;
    right: 38px;
    top: 162px;
    text-align: right;
    color: var(--text-dark);
    font-size: 14.5px;
    line-height: 18px;
  }
  .contact__name {
    font-family: "Roboto Condensed", Arial, sans-serif;
    font-weight: 500;
    font-size: 23px;
    line-height: 26px;
    color: var(--silver-mid);
    margin-bottom: 10px;
  }
  .contact__address { margin-bottom: 11px; }
  .contact__line { display: flex; justify-content: flex-end; align-items: center; gap: 10px; height: 19px; }
  .contact__icon { width: 14px; height: 14px; flex-shrink: 0; fill: var(--silver-mid); }

  .web-band {
    position: absolute;
    left: 0; bottom: 0;
    width: 100%;
    height: 45px;
    background: linear-gradient(90deg, #d4d4d4 0%, #8e8e8e 35%, #9a9a9a 65%, #d8d8d8 100%);
    display: flex;
    align-items: center;
    justify-content: center;
  }
  .web-band__text {
    font-family: "Michroma", Arial, sans-serif;
    font-size: 15px;
    letter-spacing: 3px;
    color: var(--white);
  }
</style>
</head>
<body>
  <section class="card card--front">
    <div class="brand">
      <span class="brand__name">KVTL</span>
      <span class="brand__mark"></span>
    </div>
    <p class="front__web">www.agentur-kvtl.de</p>
  </section>

  <section class="card card--back">
    <div class="brand">
      <span class="brand__mark"></span>
      <span class="brand__name">KVTL</span>
    </div>
    <div class="contact">
      <p class="contact__name">LUKAS BRANDT</p>
      <p class="contact__address">Kellberger Str. 18<br>73614 Schorndorf</p>
      <p class="contact__line">07146-839214-0
        <svg class="contact__icon" viewBox="0 0 24 24" aria-hidden="true"><path d="M6.6 10.8a15.1 15.1 0 0 0 6.6 6.6l2.2-2.2a1 1 0 0 1 1-.25 11.4 11.4 0 0 0 3.6.6 1 1 0 0 1 1 1V20a1 1 0 0 1-1 1A17 17 0 0 1 3 4a1 1 0 0 1 1-1h3.5a1 1 0 0 1 1 1c0 1.25.2 2.45.6 3.6a1 1 0 0 1-.25 1z"/></svg>
      </p>
      <p class="contact__line">lukas@agentur-kvtl.de
        <svg class="contact__icon" viewBox="0 0 24 24" aria-hidden="true"><rect x="2" y="5" width="20" height="14" rx="1.5"/><path d="M3 6.5l9 6.5 9-6.5" fill="none" stroke="#f3f3f3" stroke-width="1.8"/></svg>
      </p>
    </div>
    <div class="web-band">
      <span class="web-band__text">WWW.AGENTUR-KVTL.DE</span>
    </div>
  </section>
</body>
</html>
```